Business Cards - New Logo Rebranding

Hello We know have a red and blue logo and are looking to create new cards. We are looking for the best creativity of the new logo merged with some of the existing artwork provided.

Target Market(s)

Realtors

Industry/Entity Type

Real Estate

Contact Information for Business Card

New logo with rebranded colors

Requirements
Must have
• Creative use of the new logo

```html
<!DOCTYPE html>
<html lang="en">
<head>
<meta charset="utf-8">
<title>Summit Crest Business Cards</title>
<link href="https://fonts.googleapis.com/css2?family=Open+Sans:wght@400;600;700;800&display=swap" rel="stylesheet">
<style>
  :root {
    --blue: #0a87c9;
    --red: #d95a5a;
    --ink: #555a60;
    --white: #ffffff;
    --bg: #e9eaec;
    --faint-blue: #dcecf7;
    --faint-red: #f6dede;
  }
  * { margin: 0; padding: 0; box-sizing: border-box; }
  html, body { width: 1200px; height: 1108px; overflow: hidden; background: var(--bg); font-family: 'Open Sans', sans-serif; }
  .stage { position: relative; width: 1200px; height: 1108px; }
  .card { position: absolute; top: 134px; width: 480px; height: 840px; border-radius: 34px; overflow: hidden; background: var(--white); box-shadow: 0 12px 30px rgba(0,0,0,.18); }
  .card--front { left: 60px; }
  .card--back { left: 660px; }
  .card svg.art { position: absolute; inset: 0; }

  .brand { position: absolute; left: 22px; top: 34px; width: 120px; display: flex; flex-direction: column; align-items: center; gap: 6px; }
  .brand__dot { width: 44px; height: 44px; border-radius: 50%; background: var(--red); }
  .brand__name { font-weight: 700; font-size: 15px; color: var(--blue); line-height: 1; white-space: nowrap; }
  .brand__tag { font-size: 7px; font-weight: 600; color: var(--blue); letter-spacing: .4px; text-transform: uppercase; white-space: nowrap; }

  .photo { position: absolute; left: 190px; top: 50px; width: 260px; height: 320px; border-radius: 130px 130px 0 0; background: linear-gradient(180deg, #c9a48a 0%, #a57c66 45%, #2f3fae 70%, #25339a 100%); }

  .identity { position: absolute; left: 0; right: 0; top: 480px; text-align: center; }
  .identity__name { font-size: 44px; font-weight: 700; line-height: 1.1; }
  .identity__first { color: var(--blue); }
  .identity__last { color: var(--red); }
  .identity__title { font-size: 22px; color: var(--ink); margin-top: 2px; }

  .contact-icons { position: absolute; top: 590px; left: 0; right: 0; display: flex; justify-content: center; gap: 12px; }
  .contact-icons span { width: 28px; height: 28px; border-radius: 50%; background: var(--red); display: flex; align-items: center; justify-content: center; }
  .contact-list { position: absolute; top: 630px; left: 0; right: 0; text-align: center; font-size: 21px; color: var(--ink); line-height: 1.3; }
  .contact-list strong { color: var(--red); font-weight: 700; }

  .services { position: absolute; left: 0; right: 0; bottom: 0; height: 72px; padding: 0 24px 6px; background: var(--blue); color: var(--white); font-size: 14px; font-weight: 600; letter-spacing: .3px; display: flex; align-items: center; justify-content: center; white-space: nowrap; }

  .headline { position: absolute; top: 40px; left: 0; right: 0; text-align: center; color: var(--white); font-weight: 800; font-size: 28px; line-height: 1.25; letter-spacing: .5px; }
  .why { position: absolute; top: 200px; left: 0; right: 0; text-align: center; color: var(--red); font-size: 31px; font-weight: 600; }
  .benefits { position: absolute; top: 262px; left: 44px; right: 24px; list-style: none; color: #444; font-size: 21px; line-height: 1.25; }
  .benefits li { position: relative; padding-left: 38px; margin-bottom: 10px; }
  .benefits li::before { content: ""; position: absolute; left: 0; top: 3px; width: 24px; height: 24px; border-radius: 50%; background: var(--blue); border: 3px solid var(--faint-red); }

  .badge { position: absolute; }
  .badge--round { border-radius: 50%; }
</style>
</head>
<body>
<main class="stage">

  <section class="card card--front">
    <svg class="art" width="480" height="840" viewBox="0 0 480 840" aria-hidden="true">
      <circle cx="320" cy="210" r="165" fill="none" stroke="var(--faint-red)" stroke-width="14"/>
      <circle cx="320" cy="210" r="138" fill="var(--faint-blue)"/>
    </svg>
    <div class="photo" role="img" aria-label="Portrait of the inspector smiling in a blue polo shirt"></div>
    <svg class="art" width="480" height="840" viewBox="0 0 480 840" aria-hidden="true">
      <polygon points="0,300 480,390 480,400 0,310" fill="var(--red)"/>
      <polygon points="0,318 480,408 480,476 0,386" fill="var(--blue)"/>
    </svg>
    <div class="brand">
      <span class="brand__dot"></span>
      <span class="brand__name">SUMMIT CREST</span>
      <span class="brand__tag">Inspection Professionals</span>
    </div>

    <div class="identity">
      <div class="identity__name"><span class="identity__first">Dan</span> <span class="identity__last">Moreno</span></div>
      <div class="identity__title">Certified Mold Inspector</div>
    </div>
    <div class="contact-icons">
      <span><svg width="14" height="14" viewBox="0 0 24 24"><path d="M6 2l4 4-2 3a12 12 0 006 6l3-2 4 4-3 4C9 21 3 15 2 5z" fill="#fff"/></svg></span>
      <span><svg width="14" height="14" viewBox="0 0 24 24"><rect x="6" y="2" width="12" height="20" rx="2" fill="none" stroke="#fff" stroke-width="2.5"/></svg></span>
      <span><svg width="14" height="14" viewBox="0 0 24 24"><rect x="2" y="5" width="20" height="14" fill="none" stroke="#fff" stroke-width="2.5"/><path d="M2 5l10 8 10-8" fill="none" stroke="#fff" stroke-width="2.5"/></svg></span>
      <span><svg width="14" height="14" viewBox="0 0 24 24"><circle cx="12" cy="12" r="9" fill="none" stroke="#fff" stroke-width="2.5"/><path d="M3 12h18M12 3c-5 6-5 12 0 18M12 3c5 6 5 12 0 18" fill="none" stroke="#fff" stroke-width="2"/></svg></span>
    </div>
    <div class="contact-list">
      800.555.0142<br>
      562.555.0187<br>
      dan@summitcrestinspect.com<br>
      www.<strong>SummitCrestInspect</strong>.com
    </div>
    <div class="services">HOME · SEWER · MOLD · COMMERCIAL · TERMITE · ROOF</div>
  </section>

  <section class="card card--back">
    <svg class="art" width="480" height="840" viewBox="0 0 480 840" aria-hidden="true">
      <circle cx="240" cy="440" r="200" fill="none" stroke="var(--faint-red)" stroke-width="14"/>
      <circle cx="240" cy="440" r="170" fill="#eef5fb"/>
      <polygon points="0,130 240,196 480,150 480,172 240,218 0,152" fill="var(--blue)"/>
      <polygon points="0,0 480,0 480,150 240,196 0,130" fill="var(--red)"/>
      <path d="M0,600 C120,640 260,720 480,680 L480,840 L0,840 Z" fill="var(--blue)"/>
    </svg>
    <div class="headline">CALIFORNIA'S #1<br>INSPECTION COMPANY!</div>
    <div class="why">Why Choose Summit Crest...</div>
    <ul class="benefits">
      <li>Performing Inspections Since 1984</li>
      <li>HomeCert Certified Master / Professional Inspectors®</li>
      <li>500,000+ Inspections Completed Statewide</li>
      <li>Request of Repairs Pricer Report</li>
      <li>90-Day Inspection Guarantees</li>
      <li>NAB Drone Licensed Roof Inspectors upon request</li>
      <li>5,000+ 5-Star Reviews on SearchMap &amp; ReviewHub</li>
    </ul>
    <span class="badge badge--round" style="left:60px;top:640px;width:70px;height:70px;background:var(--red);border:4px solid #fff;"></span>
    <span class="badge badge--round" style="left:200px;top:660px;width:74px;height:74px;background:#c9a53a;"></span>
    <span class="badge badge--round" style="left:350px;top:680px;width:72px;height:72px;background:#bdb9a8;"></span>
    <span class="badge" style="left:40px;top:745px;width:130px;height:48px;background:#2a2f7a;border:3px solid #c9a53a;border-radius:24px 6px 6px 24px;"></span>
    <span class="badge" style="left:210px;top:760px;width:90px;height:44px;background:var(--red);border-radius:6px;"></span>
    <span class="badge badge--round" style="left:370px;top:770px;width:46px;height:46px;background:#fff;"></span>
  </section>

</main>
</body>
</html>
```